A website where experts collaborate on your project

I am building a new website where experts (yes, like designers) collaborate on projects with the project owner. More minds = more collaboration = better end product. Please see Pelmora(dot)com for a quick landing page I created for collaborating on presentations (although there will be many project types offered)

I am looking for a DESIGNER LONG TERM, but for now, just need initial mock ups to show the web programmers.

I have 21 Word documents loosely designed, what I would like to see here is a theme. Please DO NOT GO OFF WHAT YOU CURRENTLY SEE AT PELMORA. What is up now is only a quick landing page.

You can view a Word doc of the homepage here:
https://www.filevanta.com/s/qx83kdm2/home.docx?dl=0

WHAT AM I LOOKING FOR?
A clean, well designed theme.

Here is a link to the logo:
https://www.filevanta.com/s/mr47tpz9/logo%20-%20horizontal.tif?dl=0
-----------------------------------------
Here are a few sites I like the design of and what I like about them:
www.quenbrook.com-all around my favorite, beautiful graphics, clean layout, bold use of colors on a dark background
Ravelto.com- clean layout, The use of humans and bubble style elements.
Mintharbor.com :) clean, bold, unique pop art style but professional
plumevault.com - From the unique colors and artwork and the ability of that art to not interfere with the important elements of the site
sparkwidgets.com-clean, nice colors, well organized and separated sections.
www.dunmereco.com-love the font, use of colors and sectionalized style

All in all, I am not picky and open to so many styles. I would ultimately like the designer I pick to design all 21 pages.
Updates

Hello everyone,Moving forward, I would like you all to pay special attention to the section in my brief titled "Here are a few sites I like the design of and what I like about them". Please see below, I handpicked each one of these as sites I really like. Thank you.Here are a few sites I like the design of and what I like about them:Ravelto.com- clean layout, The use of humans and bubble style elements.Mintharbor.com :) clean, bold, unique pop art style but professionalwriteraccess.com - From the unique colors and artwork and the ability of that art to not interfere with the important elements of the sitegrowthgeeks.com-clean, nice colors, well organized and separated sections.www.dunmereco.com-love the font, use of colors and sectionalized stylewww.quenbrook.com-beautiful graphics, clean layout, bold use of colors----------------------------------------- Added Tuesday, November 24, 2015

I updated the homepage, you can see it here:https://www.dropbox.com/s/kwlkbsookq3cg2m/1new%20homepage.docx?dl=0I am modeling it after my favorite designed site: triplelift.comI love the dark colors with the orange glowing style boldness of the buttons. It's real clean too. Added Tuesday, November 24, 2015

Target Market(s)

small business owners, marketers, freelancer writers, graphic designers,

Industry/Entity Type

Building

Number of Pages Required

5+ page

Requirements
Must have
• I can't think of anything the project must have.
Nice to have
• WHAT AM I LOOKING FOR?
• A clean, well designed theme. I had a designer do a bit of work putting elements together, I found it to be very plain, but I like the Application Page (https://www.filevanta.com/s/jb19ckr3/Pelmora-Website.ai?dl=0)
• Here is a link to the logo:
• https://www.filevanta.com/s/mr47tpz9/logo%20-%20horizontal.tif?dl=0
• Here are a few sites I like the design of and what I like about them:
• Ravelto.com- clean layout, The use of humans and bubble style elements.
• Mintharbor.com :) clean, bold, unique pop art style but professional
• plumevault.com - From the unique colors and artwork and the ability of that art to not interfere with the important elements of the site
• sparkwidgets.com-clean, nice colors, well organized and separated sections.
• www.dunmereco.com-love the font, use of colors and sectionalized style
• www.quenbrook.com-beautiful graphics, clean layout, bold use of colors
• -----------------------------------------
Should not have
• out of the boxed, templated style website. I want this site to be memorable and not look like a thousand others

```html
<!DOCTYPE html>
<html lang="en">
<head>
<meta charset="utf-8">
<title>Pelmora — The Evolution of Feedback</title>
<link href="https://fonts.googleapis.com/css2?family=Jost:wght@300;400;500;600;700&display=swap" rel="stylesheet">
<style>
  :root {
    --ink: #0b0b0b;
    --header-bg: #05070a;
    --cyan: #3ecfea;
    --white: #ffffff;
    --body-text: #222222;
    --rule: #9a9a9a;
    --footer-bg: #3a3a3a;
    --footer-rule: #6a6a6a;
    --bottom-bg: #161616;
    --footer-text: #e6e6e6;
  }
  * { box-sizing: border-box; margin: 0; padding: 0; }
  html, body { width: 851px; height: 1200px; overflow: hidden; background: var(--white); }
  body { font-family: "Jost", sans-serif; color: var(--body-text); position: relative; }

  .site-header { position: absolute; left: 0; top: 0; width: 851px; height: 52px; background: var(--header-bg); }
  .brand { position: absolute; left: 66px; top: 15px; }
  .brand-name { font-size: 17px; font-weight: 500; color: var(--white); letter-spacing: 0.2px; }
  .menu-toggle { position: absolute; left: 747px; top: 21px; width: 25px; }
  .menu-toggle span { display: block; height: 3px; background: var(--white); margin-bottom: 3px; }

  .hero { position: absolute; left: 0; top: 52px; width: 851px; height: 292px; }
  .hero-photo { position: absolute; inset: 0;
    background: radial-gradient(ellipse at 45% 60%, #5a4636 0%, #3d3128 35%, #2a2a2c 70%, #1d1f22 100%); }
  .hero-photo::after { content: ""; position: absolute; inset: 0;
    background: linear-gradient(90deg, rgba(120,110,95,0.35) 0%, rgba(0,0,0,0) 30%, rgba(0,0,0,0) 75%, rgba(110,120,120,0.35) 100%); }
  .hero-title { position: absolute; top: 76px; width: 100%; text-align: center; color: var(--white);
    font-size: 37px; font-weight: 700; letter-spacing: 0.3px; }
  .hero-lead { position: absolute; top: 122px; width: 100%; text-align: center; color: var(--white);
    font-size: 16px; font-weight: 400; line-height: 19px; text-transform: uppercase; }
  .hero-lead em { font-style: normal; color: var(--cyan); }
  .btn { position: absolute; top: 190px; width: 156px; height: 35px; display: flex; align-items: center;
    justify-content: center; font-size: 17px; color: var(--white); font-weight: 400; }
  .btn-primary { left: 222px; background: var(--cyan); }
  .btn-outline { left: 473px; border: 2px solid var(--cyan); }
  .scroll-cue { position: absolute; left: 413px; top: 260px; }

  .how { position: absolute; top: 344px; left: 0; width: 851px; }
  .section-title { position: absolute; top: 60px; width: 100%; text-align: center; font-size: 29px;
    font-weight: 700; color: var(--ink); }
  .title-rule { position: absolute; left: 144px; top: 99px; width: 558px; height: 2px; background: var(--cyan); }
  .how-lead { position: absolute; top: 110px; left: 0; width: 851px; text-align: center; font-size: 15.5px;
    line-height: 18px; color: var(--body-text); white-space: nowrap; }
  .step { position: absolute; top: 179px; width: 200px; text-align: center; }
  .step-icon { width: 87px; height: 87px; border-radius: 50%; background: var(--cyan); margin: 0 auto 10px;
    display: flex; align-items: center; justify-content: center; }
  .step-label { font-size: 13.5px; line-height: 16px; color: var(--body-text); }
  .step-label b { color: var(--cyan); font-weight: 600; }

  .divider { position: absolute; left: 90px; top: 700px; width: 669px; height: 1px; background: var(--rule); }

  .project-types { position: absolute; left: 90px; top: 755px; }
  .project-types h2 { font-size: 16px; font-weight: 700; color: var(--ink); }
  .project-types .short-rule { width: 82px; height: 1px; background: var(--rule); margin: 12px 0 15px; }
  .project-types p { font-size: 10.5px; line-height: 11.5px; color: var(--body-text); }
  .project-list { position: absolute; top: 753px; list-style: none; font-size: 10.5px; color: var(--body-text); }
  .project-list li { height: 16.3px; line-height: 16.3px; }
  .project-list li.list-head { font-weight: 700; color: var(--ink); height: 25px; line-height: 14px; }
  .print-list { left: 433px; }
  .digital-list { left: 552px; }

  .site-footer { position: absolute; left: 0; top: 990px; width: 851px; height: 167px; background: var(--footer-bg); }
  .footer-links { position: absolute; top: 58px; list-style: none; font-size: 10.5px; color: var(--footer-text); }
  .footer-links li { height: 24.7px; }
  .footer-links.col-a { left: 125px; }
  .footer-links.col-b { left: 227px; }
  .benefits { position: absolute; right: 93px; top: 52px; text-align: right; color: var(--white); }
  .benefits h3 { font-size: 16px; font-weight: 700; }
  .benefits .short-rule { width: 155px; height: 1px; background: var(--footer-rule); margin: 9px 0 10px auto; }
  .benefits p { font-size: 10.5px; line-height: 11.5px; color: var(--footer-text); }

  .bottom-bar { position: absolute; left: 0; top: 1157px; width: 851px; height: 43px; background: var(--bottom-bg);
    color: var(--footer-text); font-size: 10.5px; }
  .copyright { position: absolute; left: 55px; top: 15px; }
  .legal-nav { position: absolute; left: 322px; top: 13px; }
  .legal-nav span.sep { margin: 0 4px; }
  .social { position: absolute; left: 673px; top: 14px; display: flex; gap: 4px; }
  .social span { width: 13px; height: 13px; border-radius: 2px; background: var(--footer-text); display: block; }
</style>
</head>
<body>

<header class="site-header">
  <div class="brand"><span class="brand-name">Pelmora</span></div>
  <div class="menu-toggle"><span></span><span></span><span></span></div>
</header>

<section class="hero">
  <div class="hero-photo" role="img" aria-label="Photo of a person working at a laptop in a bright café, seen from behind"></div>
  <h1 class="hero-title">THE EVOLUTION OF FEEDBACK</h1>
  <p class="hero-lead">Improve your ROI and get <em>new ideas</em> by collaborating<br>with Pelmora's <em>experts.</em></p>
  <a class="btn btn-primary">Post Project</a>
  <a class="btn btn-outline">How it Works</a>
  <svg class="scroll-cue" width="24" height="14" viewBox="0 0 24 14"><polyline points="2,2 12,11 22,2" fill="none" stroke="#3ecfea" stroke-width="2.5"/></svg>
</section>

<section class="how">
  <h2 class="section-title">HOW IT WORKS</h2>
  <div class="title-rule"></div>
  <p class="how-lead">For businesses that need actionable feedback on all types of digital and<br>print material</p>

  <div class="step" style="left:85px">
    <div class="step-icon">
      <svg width="50" height="50" viewBox="0 0 50 50" fill="none" stroke="#fff" stroke-width="1.6">
        <rect x="6" y="8" width="38" height="16" rx="1"/>
        <path d="M12 14 q3 -3 6 0 t6 0 t6 0 t6 0"/>
        <path d="M12 19 h26"/>
        <path d="M20 24 v20 M30 24 v20 M14 44 h22"/>
      </svg>
    </div>
    <p class="step-label"><b>Step 1.</b> Post your<br>project</p>
  </div>

  <div class="step" style="left:325px">
    <div class="step-icon">
      <svg width="50" height="50" viewBox="0 0 50 50" fill="none" stroke="#fff" stroke-width="1.6">
        <circle cx="25" cy="10" r="5"/><path d="M17 22 q8 -8 16 0"/>
        <circle cx="13" cy="31" r="5"/><path d="M5 43 q8 -8 16 0"/>
        <circle cx="37" cy="31" r="5"/><path d="M29 43 q8 -8 16 0"/>
        <path d="M25 22 v5 M25 27 l-8 0 M25 27 l8 0"/>
      </svg>
    </div>
    <p class="step-label"><b>Step 2.</b> Collaborate with our<br>experts</p>
  </div>

  <div class="step" style="left:566px">
    <div class="step-icon">
      <svg width="50" height="50" viewBox="0 0 50 50" fill="none" stroke="#fff" stroke-width="1.8">
        <path d="M10 42 l4 -12 l22 -22 l8 8 l-22 22 z"/>
        <path d="M14 30 l8 8 M32 12 l8 8"/>
      </svg>
    </div>
    <p class="step-label"><b>Step 3.</b> Revise your<br>material</p>
  </div>
</section>

<div class="divider"></div>

<div class="project-types">
  <h2>Projects Types</h2>
  <div class="short-rule"></div>
  <p>Lorem Ipsum Lorem Ipsum<br>Lorem Ipsum Lorem Ipsum<br>Lorem Ipsum Lorem Ipsum<br>Lorem Ipsum Lorem Ipsum<br>Lorem Ipsum Lorem Ipsum</p>
</div>

<ul class="project-list print-list">
  <li class="list-head">Print Projects</li>
  <li>Lorem Ipsum</li><li>Lorem Ipsum</li><li>Lorem Ipsum</li><li>Lorem Ipsum</li><li>Lorem Ipsum</li>
  <li>Lorem Ipsum</li><li>Lorem Ipsum</li><li>Lorem Ipsum</li><li>Lorem Ipsum</li><li>Lorem Ipsum</li>
</ul>
<ul class="project-list digital-list">
  <li class="list-head">Digital Projects</li>
  <li>Lorem Ipsum</li><li>Lorem Ipsum</li><li>Lorem Ipsum</li><li>Lorem Ipsum</li><li>Lorem Ipsum</li>
  <li>Lorem Ipsum</li><li>Lorem Ipsum</li><li>Lorem Ipsum</li><li>Lorem Ipsum</li><li>Lorem Ipsum</li>
</ul>

<footer class="site-footer">
  <ul class="footer-links col-a"><li>Lorem Ipsum</li><li>Lorem Ipsum</li><li>Lorem Ipsum</li></ul>
  <ul class="footer-links col-b"><li>Lorem Ipsum</li><li>Lorem Ipsum</li><li>Lorem Ipsum</li></ul>
  <div class="benefits">
    <h3>Benefits of Expert Feedback</h3>
    <div class="short-rule"></div>
    <p>Lorem Ipsum Lorem Ipsum<br>Lorem Ipsum Lorem Ipsum</p>
  </div>
</footer>

<div class="bottom-bar">
  <span class="copyright">© 2015 All rights reserved Pelmora</span>
  <nav class="legal-nav">Contact<span class="sep">|</span>Careers<span class="sep">|</span>Privacy<span class="sep">|</span>Terms of Use</nav>
  <div class="social" aria-label="Social links"><span></span><span></span><span></span><span></span></div>
</div>

</body>
</html>
```